BUSINESS CARD DESIGN

NAME- DALE VORSKIN
PHONE NUMER - 555- 714-9082
EMAIL- OFFICE@TRV-GROUNDMAKRZ.COM
BACK OF CARD- SPEACIALIZES IN LAND CLEARING, FORESTRY MUCLHING AND EXCAVATION

Contact Information for Business Card

NAME- DALE VORSKIN PHONE NUMER - 555- 714-9082 EMAIL- OFFICE@TRV-GROUNDMAKRZ.COM BACK OF CARD- SPEACIALIZES IN LAND CLEARING , MUCLHING AND EXCAVATION

```html
<!DOCTYPE html>
<html lang="en">
<head>
<meta charset="utf-8">
<title>Traverse Groundmakrz – Business Card</title>
<link rel="stylesheet" href="https://fonts.googleapis.com/css2?family=Roboto:wght@300;400;700&family=Roboto+Condensed:wght@400&display=swap">
<style>
  :root{
    --page:#e3e7e8;
    --gold:#f5b31c;
    --gold-deep:#e0a010;
    --ink:#212125;
    --paper:#ffffff;
    --soft:#e6e6e6;
  }
  *{margin:0;padding:0;box-sizing:border-box}
  html,body{width:1200px;height:960px;overflow:hidden;background:var(--page)}
  .card{
    position:absolute;left:250px;width:702px;height:401px;border-radius:22px;overflow:hidden;
  }
  .card--front{top:60px;background:var(--gold)}
  .card--back{top:500px;background:var(--ink)}

  .brand{
    position:absolute;display:flex;flex-direction:column;align-items:center;gap:12px;
    font-family:"Roboto Condensed",sans-serif;font-weight:400;text-align:center;
    letter-spacing:3px;line-height:1.15;
  }
  .brand__dot{width:64px;height:64px;border-radius:50%}
  .card--front .brand{left:0;right:0;top:88px;color:var(--gold-deep);font-size:30px}
  .card--front .brand__dot{background:var(--gold-deep)}
  .card--back .brand{left:42px;width:270px;top:108px;color:var(--gold);font-size:24px}
  .card--back .brand__dot{background:var(--gold)}

  .tagline{
    position:absolute;left:0;right:0;top:356px;text-align:center;
    font-family:"Roboto Condensed",sans-serif;font-size:16.5px;color:var(--paper);letter-spacing:.3px;
  }
  .divider{position:absolute;left:350px;top:84px;width:1px;height:235px;background:var(--gold)}
  .person{
    position:absolute;left:389px;top:138px;font-family:"Roboto",sans-serif;font-size:36px;
    color:var(--gold);letter-spacing:.5px;white-space:nowrap;
  }
  .person__first{font-weight:700}
  .person__last{font-weight:300}
  .contact{position:absolute;left:390px;top:212px;list-style:none}
  .contact__item{
    display:flex;align-items:center;gap:12px;height:28px;
    font-family:"Roboto",sans-serif;font-size:15.5px;color:var(--soft);letter-spacing:.8px;
  }
  .contact__icon{width:17px;height:17px;flex:none}
  .website{
    position:absolute;left:0;right:0;top:356px;text-align:center;padding-left:12px;
    font-family:"Roboto",sans-serif;font-size:15.5px;color:var(--gold);letter-spacing:.4px;
  }
</style>
</head>
<body>
  <section class="card card--front">
    <div class="brand">
      <span class="brand__dot"></span>
      <span class="brand__name">TRAVERSE GROUNDMAKRZ<br>LLC</span>
    </div>
    <p class="tagline">SPEACIALIZES IN LAND CLEARING , MUCLHING AND EXCAVATION</p>
  </section>

  <section class="card card--back">
    <div class="brand">
      <span class="brand__dot"></span>
      <span class="brand__name">TRAVERSE GROUNDMAKRZ<br>LLC</span>
    </div>
    <span class="divider"></span>
    <h1 class="person"><span class="person__first">DALE</span> <span class="person__last">VORSKIN</span></h1>
    <ul class="contact">
      <li class="contact__item">
        <svg class="contact__icon" viewBox="0 0 24 24" aria-hidden="true"><path fill="var(--gold)" d="M6.6 10.8a15.1 15.1 0 0 0 6.6 6.6l2.2-2.2a1 1 0 0 1 1-.25 11.4 11.4 0 0 0 3.6.57 1 1 0 0 1 1 1V20a1 1 0 0 1-1 1A17 17 0 0 1 3 4a1 1 0 0 1 1-1h3.5a1 1 0 0 1 1 1c0 1.25.2 2.45.57 3.57a1 1 0 0 1-.25 1z"/></svg>
        555- 714-9082
      </li>
      <li class="contact__item">
        <svg class="contact__icon" viewBox="0 0 24 24" aria-hidden="true"><path fill="var(--gold)" d="M2 9l10-7 10 7v12H2z"/><path fill="var(--ink)" d="M4 10.2l8 5.3 8-5.3V19H4z"/><circle cx="12" cy="9" r="2.6" fill="none" stroke="var(--ink)" stroke-width="1.4"/></svg>
        OFFICE@TRV-GROUNDMAKRZ.COM
      </li>
    </ul>
    <p class="website">WWW.TRV-GROUNDMAKRZ.COM</p>
  </section>
</body>
</html>
```